Simple Logo Design for Semi-Clear Plastic Frosted Card stock

Create a business card on frosted plastic. compliment existing logo elements with a tree trunk, roots, or seed at the lower half and the full logo both on the front.

Contact information will go on a solid portion of the back of this design since this card stock is semi-transparent.

It is important to consider this plastic card stock medium in your design. I found helpful tips and guides listed at vellaprint-sample.net: be careful to understand ink printed on plastic cards cannot have too much of a consistent print area or risks peeling and fine lines can easily scratch off.
Updates

2" x 3.5" 20PT Clear Plastic Business cards with Round corners Please get info or templates here: https://www.vellaprint-sample.net/product-detail/2-x-35-20pt-clear-plastic-business-cards-with-round-corners

Target Market(s)

Not for profit- religion

Industry/Entity Type

Business

Must include complementary elements to the existing logo

Font styles to use
Decorative

Colors
000000

Requirements
Must have
• Elements of community, nature and oneness. Such as: seed, roots, tree trunk, etc.
• Three lines of space on the back for Name, Title, Phone Number.
Nice to have
• I like a light use of decorative elements
Should not have
• No eyes, from faces or animals.

```html
<!DOCTYPE html>
<html lang="en">
<head>
<meta charset="utf-8">
<title>Stillwater Circle – Business Card</title>
<link href="https://fonts.googleapis.com/css2?family=Montserrat:wght@500;600&family=Questrial&display=swap" rel="stylesheet">
<style>
  :root {
    --page-bg: #d9d6d1;
    --frost-light: #f1f3f2;
    --frost-mid: #dfe4e3;
    --frost-edge: #c3cbc9;
    --band-teal: #1f4f4b;
    --band-teal-deep: #153a37;
    --swoosh-green: #2f7a2c;
    --name-ink: #e8efee;
    --brand-green: #245c47;
    --tagline-ink: #2a5d3b;
    --phone-ink: #222222;
  }
  html, body {
    margin: 0;
    width: 1200px;
    height: 969px;
    overflow: hidden;
    background: var(--page-bg);
  }
  .canvas {
    position: relative;
    width: 1200px;
    height: 969px;
  }
  .business-card {
    position: absolute;
    left: 100px;
    top: 201px;
    width: 1000px;
    height: 567px;
    filter: drop-shadow(0 14px 26px rgba(0,0,0,0.18));
  }
  .card-name { font-family: "Montserrat", sans-serif; font-weight: 600; letter-spacing: 0.5px; }
  .card-title { font-family: "Montserrat", sans-serif; font-weight: 500; letter-spacing: 0.4px; }
  .brand-name { font-family: "Questrial", sans-serif; letter-spacing: 0.6px; }
  .brand-tagline { font-family: "Questrial", sans-serif; letter-spacing: 0.8px; }
  .card-phone { font-family: "Questrial", sans-serif; letter-spacing: 0.5px; }
</style>
</head>
<body>
<main class="canvas">
  <svg class="business-card" viewBox="0 0 550 312" role="img" aria-label="Frosted plastic business card for Stillwater Circle">
    <defs>
      <linearGradient id="frost" x1="0" y1="0" x2="1" y2="1">
        <stop offset="0" stop-color="var(--frost-light)"/>
        <stop offset="0.6" stop-color="var(--frost-mid)"/>
        <stop offset="1" stop-color="#e9ecea"/>
      </linearGradient>
      <linearGradient id="band" x1="0" y1="0" x2="1" y2="0">
        <stop offset="0" stop-color="var(--band-teal)"/>
        <stop offset="1" stop-color="var(--band-teal-deep)"/>
      </linearGradient>
      <clipPath id="card-shape">
        <rect x="0" y="0" width="550" height="312" rx="16" ry="16"/>
      </clipPath>
    </defs>

    <g clip-path="url(#card-shape)">
      <rect class="card-body" x="0" y="0" width="550" height="312" fill="url(#frost)"/>
      <path class="top-band" d="M0,0 H550 V160 C450,100 290,40 0,34 Z" fill="url(#band)"/>
      <path class="green-swoosh" d="M0,34 C290,40 450,100 550,160 V168 C450,110 290,46 0,38 Z" fill="var(--swoosh-green)"/>
    </g>
    <rect x="0.5" y="0.5" width="549" height="311" rx="16" ry="16" fill="none" stroke="var(--frost-edge)" stroke-width="1"/>

    <text class="card-name" x="525" y="40" text-anchor="end" font-size="17" fill="var(--name-ink)">ALAN REYES</text>
    <text class="card-title" x="525" y="64" text-anchor="end" font-size="13" fill="var(--name-ink)">PRESIDENT</text>

    <circle class="brand-mark" cx="147" cy="200" r="20" fill="var(--brand-green)"/>
    <text class="brand-name" x="147" y="250" text-anchor="middle" font-size="23" fill="var(--brand-green)">STILLWATER CIRCLE</text>
    <text class="brand-tagline" x="147" y="265" text-anchor="middle" font-size="7.5" fill="var(--tagline-ink)">LEARNING, FELLOWSHIP &amp; CALM</text>

    <text class="card-phone" x="525" y="262" text-anchor="end" font-size="22" fill="var(--phone-ink)">555 0142 7788</text>
  </svg>
</main>
</body>
</html>
```